My Web Development Portfolio site

I'm a web developer and I need a web design that can showcase my web development portfolio. I like most of the websites from this link: http://www.lumivexa.com/portfolios/examples-503917. My ideal design should be modern, clean and fun. I will let the designer decided the color theme for the website.

Target Market(s)

Potential Employers.

Number of Pages Required

1 page

Requirements
Must have
• - Menu bar that includes at least: About Me, Blog, Contact, Project/Work
• - Excellent color theme
• - Use the logo I provided (see attachment)
Nice to have
• - Some animation
• - Fun yet modern design

```html
<!DOCTYPE html>
<html lang="en">
<head>
<meta charset="utf-8">
<title>Codevoya — Web Development Portfolio</title>
<link rel="stylesheet" href="https://fonts.googleapis.com/css2?family=Raleway:wght@500;600;700&family=Open+Sans:wght@400;600&display=swap">
<style>
:root{
  --orange:#ee7b4a;
  --orange-dark:#c85f30;
  --ink:#555a5f;
  --ink-soft:#8a8f94;
  --body:#9a9ea3;
  --white:#ffffff;
  --footer:#1c1c1c;
  --footer-line:#333333;
  --footer-text:#8e8e8e;
  --space-deep:#040a1c;
  --space-mid:#0f2a5a;
}
*{margin:0;padding:0;box-sizing:border-box}
html,body{width:1200px;height:3237px;overflow:hidden;background:var(--white)}
body{font-family:"Open Sans",Arial,sans-serif;color:var(--ink);position:relative}
.heading{font-family:"Raleway",Arial,sans-serif;font-weight:700;letter-spacing:2px;text-transform:uppercase;text-align:center}
.rule{display:block;width:34px;height:3px;background:var(--orange);margin:0 auto}
.btn{position:absolute;left:50%;transform:translateX(-50%);display:flex;align-items:center;justify-content:center;border-radius:22px;font-family:"Raleway",Arial,sans-serif;font-weight:600;font-size:11px;letter-spacing:1px;text-transform:uppercase;color:var(--white)}
.btn-solid{background:var(--orange)}
.btn-outline{border:1.5px solid rgba(255,255,255,.8)}

/* hero */
.hero{position:absolute;left:0;top:0;width:1200px;height:624px;overflow:hidden;
  background:radial-gradient(ellipse 900px 380px at 560px 760px,#3d7fc4 0%,#1a4b8f 30%,#0b2450 55%,transparent 75%),
  radial-gradient(ellipse 420px 120px at 600px 330px,rgba(120,170,230,.45),transparent 70%),
  linear-gradient(180deg,var(--space-deep) 0%,#071633 45%,var(--space-mid) 100%)}
.brand{position:absolute;left:64px;top:24px;display:flex;flex-direction:column;align-items:center;gap:6px;color:var(--white)}
.brand-dot{width:40px;height:40px;border:3px solid var(--white);border-radius:50%}
.brand-name{font-family:"Raleway",Arial,sans-serif;font-weight:500;font-size:28px;letter-spacing:.5px}
.nav{position:absolute;top:61px;left:0;width:1200px;height:16px;font-family:"Raleway",Arial,sans-serif;font-weight:700;font-size:11.5px;letter-spacing:.5px;color:var(--white)}
.nav a{position:absolute;color:inherit;text-decoration:none}
.hero-title{position:absolute;top:238px;width:100%;color:var(--white);font-size:56px;letter-spacing:4px}
.hero-sub{position:absolute;top:314px;width:100%;text-align:center;color:var(--white);font-family:"Raleway",Arial,sans-serif;font-weight:500;font-size:25px;letter-spacing:2px;text-transform:uppercase}
.hero .btn{top:366px;width:156px;height:39px}
.scroll-cue{position:absolute;left:588px;top:528px}

/* welcome */
.welcome-title{position:absolute;top:690px;width:100%;font-size:29px;color:var(--ink)}
.welcome .rule{position:absolute;top:743px;left:583px}
.welcome-text{position:absolute;top:776px;left:190px;width:820px;text-align:center;font-size:12.5px;line-height:24px;color:var(--body)}

/* portfolio */
.section-title{position:absolute;width:100%;font-size:18px;color:var(--ink)}
.portfolio-title{top:943px}
.portfolio-rule{position:absolute;top:983px;left:583px}
.grid{position:absolute;top:1027px;left:0;width:1200px;display:grid;grid-template-columns:repeat(4,300px);grid-auto-rows:272px}
.project-thumb{width:300px;height:199px}
.project-name{margin-top:16px;text-align:center;font-family:"Raleway",Arial,sans-serif;font-weight:700;font-size:13px;letter-spacing:1px;color:var(--ink-soft);text-transform:uppercase}
.project-link{margin-top:4px;text-align:center;font-size:11px;color:#a7abaf}

/* posts */
.posts-title{top:1894px}
.posts-rule{position:absolute;top:1932px;left:583px}
.post{position:absolute;width:470px}
.post-title{font-family:"Raleway",Arial,sans-serif;font-weight:700;font-size:13.5px;letter-spacing:1px;color:var(--ink-soft);text-transform:uppercase}
.post-text{margin-top:12px;font-size:12px;line-height:24px;color:var(--body)}
.posts .btn{top:2225px;width:164px;height:39px}

/* about */
.about{position:absolute;left:0;top:2346px;width:1200px;height:384px;
  background:radial-gradient(ellipse 500px 260px at 700px 200px,rgba(255,190,150,.35),transparent 70%),
  linear-gradient(135deg,#e8915f 0%,var(--orange) 40%,#d86a3a 75%,var(--orange-dark) 100%)}
.about-title{position:absolute;top:92px;width:100%;color:var(--white);font-size:18px}
.about .rule{position:absolute;top:127px;left:583px;background:var(--white)}
.about-text{position:absolute;top:154px;left:210px;width:780px;text-align:center;font-size:11.5px;line-height:24px;color:var(--white)}
.about .btn{top:252px;width:168px;height:41px}

/* footer */
.footer{position:absolute;left:0;top:2730px;width:1200px;height:507px;background:var(--footer);color:var(--footer-text)}
.footer-brand{position:absolute;top:70px;left:0;width:100%;display:flex;flex-direction:column;align-items:center;gap:10px;color:var(--white)}
.footer-brand .brand-dot{width:44px;height:44px}
.contact-item{position:absolute;top:210px;width:300px;display:flex;flex-direction:column;align-items:center;gap:18px;font-size:12px}
.socials{position:absolute;top:328px;left:0;width:100%;display:flex;justify-content:center;gap:18px}
.social{width:52px;height:52px;border:1.5px solid #555;border-radius:50%}
.footer-line{position:absolute;top:436px;left:276px;width:648px;height:1px;background:var(--footer-line)}
.copyright{position:absolute;top:456px;width:100%;text-align:center;font-size:11px}
</style>
</head>
<body>

<header class="hero" role="img" aria-label="Night view of Earth from space with sunrise glow on the horizon">
  <div class="brand"><span class="brand-dot"></span><span class="brand-name">codevoya</span></div>
  <nav class="nav">
    <a style="left:623px">HOME</a>
    <a style="left:714px">ABOUT ME</a>
    <a style="left:830px">BLOG</a>
    <a style="left:919px">PROJECT/WORK</a>
    <a style="left:1069px">CONTACT</a>
  </nav>
  <h1 class="heading hero-title">Codevoya</h1>
  <p class="hero-sub">Lorem ipsum is simply dummy text of the printing</p>
  <a class="btn btn-solid">Contact here</a>
  <svg class="scroll-cue" width="24" height="46" viewBox="0 0 24 46"><rect x="1.5" y="1.5" width="21" height="43" rx="10.5" fill="none" stroke="#fff" stroke-opacity=".75" stroke-width="2"/><line x1="12" y1="9" x2="12" y2="16" stroke="#fff" stroke-opacity=".75" stroke-width="2"/></svg>
</header>

<section class="welcome">
  <h2 class="heading welcome-title">Welcome to Codevoya</h2>
  <span class="rule"></span>
  <p class="welcome-text">Lorem Ipsum is simply dummy text of the printing and typesetting industry. Lorem Ipsum has been the industry's standard dummy text ever since the 1500s, when an unknown printer took a galley of type and scrambled it to make a type specimen book. It has survived not only five centuries, but also the leap into electronic typesetting, remaining essentially unchanged. It was popularised in the 1960s with the release of Letraset sheets containing Lorem Ipsum passages, and more recently.</p>
</section>

<section class="portfolio">
  <h2 class="heading section-title portfolio-title">Portfolio</h2>
  <span class="rule portfolio-rule"></span>
  <div class="grid">
    <article><div class="project-thumb" role="img" aria-label="Website screenshot for a lighting studio in warm brown and amber" style="background:linear-gradient(135deg,#6b3a1e,#a4501f 60%,#2d2420)"></div><h3 class="project-name">Lorem ipsum is simply</h3><p class="project-link">Visit live page</p></article>
    <article><div class="project-thumb" role="img" aria-label="Website screenshot for a vintage auto shop in red and cream" style="background:linear-gradient(135deg,#e9e1d2,#b8322a 55%,#3a2c2a)"></div><h3 class="project-name">Lorem ipsum is simply</h3><p class="project-link">Visit live page</p></article>
    <article><div class="project-thumb" role="img" aria-label="Website screenshot for a design agency with a model on light teal" style="background:linear-gradient(135deg,#c9413a,#e8d9c8 50%,#7fc6c6)"></div><h3 class="project-name">Lorem ipsum is simply</h3><p class="project-link">Visit live page</p></article>
    <article><div class="project-thumb" role="img" aria-label="Website screenshot for a car dealership with a silver sedan" style="background:linear-gradient(135deg,#3a3f48,#8a919a 55%,#1d1f24)"></div><h3 class="project-name">Lorem ipsum is simply</h3><p class="project-link">Visit live page</p></article>
    <article><div class="project-thumb" role="img" aria-label="Black and white website screenshot for a portrait photographer" style="background:linear-gradient(135deg,#141414,#6e6e6e 55%,#cfcfcf)"></div><h3 class="project-name">Lorem ipsum is simply</h3><p class="project-link">Visit live page</p></article>
    <article><div class="project-thumb" role="img" aria-label="Website screenshot for a casino promotion in green and red" style="background:linear-gradient(135deg,#2b1a12,#b2432c 45%,#2f6a3a)"></div><h3 class="project-name">Lorem ipsum is simply</h3><p class="project-link">Visit live page</p></article>
    <article><div class="project-thumb" role="img" aria-label="Website screenshot for a coffee house with a coffee cup" style="background:radial-gradient(circle at 45% 45%,#d9a35a,#6b3a16 55%,#1d120b)"></div><h3 class="project-name">Lorem ipsum is simply</h3><p class="project-link">Visit live page</p></article>
    <article><div class="project-thumb" role="img" aria-label="Website screenshot for an outdoor gear store in dark grey and yellow" style="background:linear-gradient(135deg,#26282a,#55585b 55%,#b9a23a)"></div><h3 class="project-name">Lorem ipsum is simply</h3><p class="project-link">Visit live page</p></article>
    <article><div class="project-thumb" role="img" aria-label="Website screenshot for a fitness studio in grey and olive" style="background:linear-gradient(135deg,#6b6a5e,#a8a58a 50%,#3b3a34)"></div><h3 class="project-name">Lorem ipsum is simply</h3><p class="project-link">Visit live page</p></article>
    <article><div class="project-thumb" role="img" aria-label="Website screenshot for a burger restaurant with a burger" style="background:linear-gradient(135deg,#f2efe8,#d99a4a 55%,#8c4a22)"></div><h3 class="project-name">Lorem ipsum is simply</h3><p class="project-link">Visit live page</p></article>
    <article><div class="project-thumb" role="img" aria-label="Website screenshot for a beach resort with turquoise sea" style="background:linear-gradient(160deg,#2aa7c9,#7fd4da 50%,#f1e6c8)"></div><h3 class="project-name">Lorem ipsum is simply</h3><p class="project-link">Visit live page</p></article>
    <article><div class="project-thumb" role="img" aria-label="Website screenshot for an eyewear brand in red" style="background:linear-gradient(135deg,#f0e2d2,#c8322c 50%,#6e1714)"></div><h3 class="project-name">Lorem ipsum is simply</h3><p class="project-link">Visit live page</p></article>
  </div>
</section>

<section class="posts">
  <h2 class="heading section-title posts-title">Recent posts</h2>
  <span class="rule posts-rule"></span>
  <article class="post" style="left:99px;top:1994px"><h3 class="post-title">Lorem ipsum is simply dummy text</h3><p class="post-text">Lorem Ipsum is simply dummy text of the printing and typesetting industry. Lorem Ipsum has been the industry's standard...</p></article>
  <article class="post" style="left:630px;top:1994px"><h3 class="post-title">Lorem ipsum is simply dummy text</h3><p class="post-text">Lorem Ipsum is simply dummy text of the printing and typesetting industry. Lorem Ipsum has been the industry's standard...</p></article>
  <article class="post" style="left:99px;top:2107px"><h3 class="post-title">Lorem ipsum is simply dummy text</h3><p class="post-text">Lorem Ipsum is simply dummy text of the printing and typesetting industry. Lorem Ipsum has been the industry's standard...</p></article>
  <article class="post" style="left:630px;top:2107px"><h3 class="post-title">Lorem ipsum is simply dummy text</h3><p class="post-text">Lorem Ipsum is simply dummy text of the printing and typesetting industry. Lorem Ipsum has been the industry's standard...</p></article>
  <a class="btn btn-solid">View more posts</a>
</section>

<section class="about" role="img" aria-label="Orange-toned photo of a desk with a laptop, notebook and coffee cup">
  <h2 class="heading about-title">About Codevoya</h2>
  <span class="rule"></span>
  <p class="about-text">Lorem Ipsum is simply dummy text of the printing and typesetting industry. Lorem Ipsum has been the industry's standard dummy text ever since the 1500s, when an unknown printer took a galley of type and scrambled it to make a type specimen book. It has survived not only five centuries, but also the leap into electronic typesetting, remaining essentially unchanged.</p>
  <a class="btn btn-outline">View more details</a>
</section>

<footer class="footer">
  <div class="footer-brand"><span class="brand-dot"></span><span class="brand-name">codevoya</span></div>
  <div class="contact-item" style="left:213px">
    <svg width="26" height="34" viewBox="0 0 26 34"><path d="M13 32C13 32 2 19 2 12.5A11 11 0 0 1 24 12.5C24 19 13 32 13 32Z" fill="none" stroke="#8e8e8e" stroke-width="2"/><circle cx="13" cy="12.5" r="4" fill="none" stroke="#8e8e8e" stroke-width="2"/></svg>
    <span>120 Street name, City name, Country : 6532336</span>
  </div>
  <div class="contact-item" style="left:489px">
    <svg width="34" height="34" viewBox="0 0 34 34"><path d="M8 3L13 9L10 13C12 18 16 22 21 24L25 21L31 26L27 31C16 30 4 18 3 7Z" fill="none" stroke="#8e8e8e" stroke-width="2" stroke-linejoin="round"/><path d="M20 4A10 10 0 0 1 30 14M20 9A5 5 0 0 1 25 14" fill="none" stroke="#8e8e8e" stroke-width="2"/></svg>
    <span>(0155) 014 287</span>
  </div>
  <div class="contact-item" style="left:765px">
    <svg width="36" height="34" viewBox="0 0 36 34"><rect x="2" y="6" width="32" height="22" fill="none" stroke="#8e8e8e" stroke-width="2"/><path d="M2 6L18 19L34 6" fill="none" stroke="#8e8e8e" stroke-width="2"/></svg>
    <span>info@codevoya.co</span>
  </div>
  <div class="socials"><span class="social"></span><span class="social"></span><span class="social"></span></div>
  <div class="footer-line"></div>
  <p class="copyright">© 2016, Codevoya. All Rights Reserved.</p>
</footer>

</body>
</html>
```